SOLVE Study flyer

I need help designing a flyer for a research study that will include brain imaging in adolescents. The info is in the attached document. The study is called the Sequoia Outlook Lantern Valley Echo (SOLVE) study. Ideally this would be returned as a document that I can edit in the future as we will have several new recruitment phases (different age groups, etc. I also would love to have a logo designed as part of this project, but I recognize that might be a separate design request.

```html
<!DOCTYPE html>
<html lang="en">
<head>
<meta charset="utf-8">
<title>SOLVE Study Flyer</title>
<link rel="stylesheet" href="https://fonts.googleapis.com/css2?family=Poppins:wght@400;500;600;700;800&family=Oswald:wght@500;600&display=swap">
<style>
  :root {
    --navy: #17224f;
    --green: #3db54a;
    --white: #ffffff;
    --card: #f5f6f8;
    --ink: #1c1c24;
    --backdrop: #e3e3e3;
  }
  * { margin: 0; padding: 0; box-sizing: border-box; }
  html, body { width: 1200px; height: 2567px; overflow: hidden; background: var(--backdrop); }
  body { position: relative; font-family: "Poppins", sans-serif; }

  .flyer {
    position: absolute; left: 50px; top: 505px;
    width: 797px; height: 1128px;
    transform: scale(1.38); transform-origin: 0 0;
    overflow: hidden; background: var(--navy);
    box-shadow: 0 6px 20px rgba(0,0,0,.18);
  }
  .flyer-shapes { position: absolute; inset: 0; width: 797px; height: 1128px; }

  .family-photo {
    position: absolute; left: 478px; top: 30px; width: 300px; height: 430px;
    border-radius: 140px 140px 10px 10px;
    background: linear-gradient(180deg, #c8a58c 0%, #efe9e3 35%, #f4f1ee 70%, #3a3d4a 100%);
  }

  .headline {
    position: absolute; left: 32px; top: 58px;
    font-weight: 700; font-size: 43px; line-height: 55px; color: var(--white);
    letter-spacing: -.3px;
  }
  .headline .accent { color: var(--green); }

  .tagline {
    position: absolute; left: 32px; top: 228px; width: 426px; height: 27px;
    background: var(--green); border-radius: 14px;
    color: var(--white); font-size: 16.5px; line-height: 27px; text-align: center;
  }
  .intro {
    position: absolute; left: 32px; top: 278px; width: 436px;
    color: var(--white); font-size: 13.3px; line-height: 19px; text-align: justify;
  }

  .card {
    position: absolute; background: var(--card); border-radius: 14px;
    box-shadow: 0 3px 10px rgba(0,0,0,.08);
  }
  .card h2 { font-weight: 700; font-size: 28px; line-height: 34px; }
  .card ul { list-style: none; }
  .card li {
    position: relative; padding-left: 12px; font-size: 15.5px; line-height: 19px;
    color: var(--ink); text-align: justify;
  }
  .card li::before {
    content: ""; position: absolute; left: 0; top: 8px; width: 4px; height: 4px;
    border-radius: 50%; background: var(--green);
  }
  .card-involves { left: 32px; top: 466px; width: 375px; height: 370px; padding: 28px 18px 0 18px; }
  .card-involves h2 { color: var(--green); margin-bottom: 26px; }
  .card-involves li { margin-bottom: 18px; }
  .card-eligible { left: 424px; top: 538px; width: 341px; height: 268px; padding: 14px 26px 0 18px; }
  .card-eligible h2 { color: var(--navy); margin-bottom: 16px; }
  .card-eligible li { margin-bottom: 19px; }

  .cta-title {
    position: absolute; left: 52px; top: 898px;
    color: var(--green); font-weight: 700; font-size: 27px; line-height: 34px;
  }
  .cta-sub {
    position: absolute; left: 52px; top: 966px;
    color: var(--white); font-weight: 600; font-size: 21px;
  }
  .contact {
    position: absolute; left: 52px; top: 1030px;
    color: var(--white); font-weight: 700; font-size: 26px; line-height: 33px;
  }

  .compensation {
    position: absolute; left: 467px; top: 824px; width: 246px; height: 246px;
    border-radius: 50%; background: var(--white);
    display: flex; align-items: center; justify-content: center;
  }
  .compensation-inner {
    width: 228px; height: 228px; border-radius: 50%; background: var(--green);
    margin-left: 18px;
    display: flex; flex-direction: column; align-items: center; justify-content: center;
    color: var(--white); font-family: "Oswald", sans-serif; font-weight: 500;
  }
  .compensation-label { font-size: 21px; line-height: 24px; }
  .compensation-amount { font-size: 62px; line-height: 64px; font-weight: 600; text-align: center; }
</style>
</head>
<body>
  <article class="flyer">
    <svg class="flyer-shapes" viewBox="0 0 797 1128" aria-hidden="true">
      <rect width="797" height="1128" fill="var(--navy)"/>
      <path d="M0 360 C120 330 230 350 320 395 C420 445 520 462 610 455 C700 448 760 430 797 415 L797 1128 L0 1128 Z" fill="var(--green)"/>
      <path d="M0 430 C110 380 220 385 320 420 C420 458 520 478 620 470 C700 462 760 448 797 440 L797 900 C720 880 640 880 560 905 C470 935 380 880 250 866 C150 856 70 864 0 880 Z" fill="#ece9e6"/>
      <path d="M0 880 C70 864 150 856 250 866 C340 876 400 905 450 955 C480 975 500 960 520 930 L520 1128 L0 1128 Z" fill="var(--navy)"/>
      <path d="M250 866 C340 876 400 905 460 958 L445 960 C390 912 330 885 250 872 Z" fill="var(--green)"/>
      <path d="M640 910 C700 920 760 950 797 975 L797 955 C760 930 700 905 640 895 Z" fill="var(--green)"/>
      <path d="M0 1010 L390 1013 C420 1014 435 1025 445 1045 L462 1128 L0 1128 Z" fill="var(--white)"/>
      <path d="M0 1016 L388 1019 C414 1020 428 1030 437 1050 L455 1128 L0 1128 Z" fill="var(--green)"/>
    </svg>

    <div class="family-photo" role="img" aria-label="Photo of a smiling family: father, mother and young son in white shirts"></div>

    <h1 class="headline">
      ARE YOU THE<br>
      <span class="accent">PARENT</span> OF <span class="accent">A CHILD</span><br>
      AGE <span class="accent">10-17?</span>
    </h1>
    <p class="tagline">Do they worry or overthink negative emotions?</p>
    <p class="intro">Northvale University researchers are seeking girls age 10-17 for a study about brain activity in emotions and decision-making and how they relate to puberty, anxiety and depression.</p>

    <section class="card card-involves">
      <h2>STUDY PARTICIPATION INVOLVES:</h2>
      <ul>
        <li>One one-hour interview (online or in-person) where your child will discuss their thoughts</li>
        <li>Online questionnaires (parent and child)</li>
        <li>One two-hour visit where your child will complete an MRI scan, answer questions about their puberty stage, and have a small hair sample taken to study puberty hormones</li>
      </ul>
    </section>

    <section class="card card-eligible">
      <h2>YOUR CHILD MAY BE ELIGIBLE IF THEY:</h2>
      <ul>
        <li>Are age 10-17</li>
        <li>Tend to worry or overthink negative thoughts</li>
        <li>Have not been diagnosed with psychosis, learning problems, or autism</li>
      </ul>
    </section>

    <h2 class="cta-title">INTERESTED IN<br>PARTICIPATING?</h2>
    <p class="cta-sub">Want more information?</p>
    <p class="contact">Please contact us!<br>solvestudy@northvale.edu</p>

    <div class="compensation">
      <div class="compensation-inner">
        <span class="compensation-label">COMPENSATION</span>
        <span class="compensation-amount">UP TO<br>$ 140</span>
      </div>
    </div>
  </article>
</body>
</html>
```